RTavenor Business Cards & Letterhead

I have a logo but need a design for some new business cards. We are a Design-Build Firm that specializes in the design and construction of commercial projects.
the cards need to be professional. no cartoon stuff.
i would like to have the cards in AI format so I can update the card as needed. Logo is provided.
Our Address is: 4187 Marlowe Ct. Westbrook, Ohio 27614

```html
<!DOCTYPE html>
<html lang="en">
<head>
<meta charset="utf-8">
<title>RTavenor Business Card</title>
<link href="https://fonts.googleapis.com/css2?family=Open+Sans:wght@400;600;700;800&display=swap" rel="stylesheet">
<style>
  :root {
    --stage: #e9e6e2;
    --card: #222327;
    --pattern-dark: #1c1d20;
    --pattern-light: #34363a;
    --brand-blue: #1b78c0;
    --text-light: #f2f3f5;
    --wordmark-grey: #9a9ca0;
  }
  * { box-sizing: border-box; margin: 0; padding: 0; }
  html, body { width: 1200px; height: 780px; overflow: hidden; }
  body {
    background: var(--stage);
    font-family: "Open Sans", Arial, sans-serif;
    display: flex;
    align-items: center;
    justify-content: center;
    gap: 80px;
  }
  .card {
    width: 360px;
    height: 630px;
    border-radius: 26px;
    background: var(--card);
    position: relative;
    overflow: hidden;
    box-shadow: 0 10px 28px rgba(0,0,0,.25);
  }
  .card-back__pattern {
    position: absolute;
    inset: 0;
    background: linear-gradient(160deg, var(--pattern-light) 0%, var(--pattern-dark) 55%, var(--pattern-light) 100%);
  }
  .card-back__wordmark {
    position: absolute;
    top: 40px;
    right: 70px;
    display: flex;
    flex-direction: column;
    align-items: center;
    gap: 14px;
  }
  .card-back__name {
    writing-mode: vertical-rl;
    font-weight: 700;
    font-size: 42px;
    letter-spacing: 1px;
    color: var(--wordmark-grey);
    line-height: 1;
  }
  .brand-square {
    width: 30px;
    height: 30px;
    background: var(--brand-blue);
  }
  .card-front__logo {
    position: absolute;
    top: 110px;
    left: 0;
    right: 0;
    display: flex;
    align-items: center;
    justify-content: center;
    gap: 14px;
  }
  .card-front__logo-name {
    font-weight: 700;
    font-size: 40px;
    color: var(--brand-blue);
  }
  .card-front__logo .brand-square { width: 36px; height: 36px; }
  .card-front__details {
    position: absolute;
    left: 44px;
    right: 30px;
    bottom: 60px;
    color: var(--text-light);
  }
  .holder-name {
    font-weight: 800;
    font-size: 28px;
    letter-spacing: .5px;
    color: var(--brand-blue);
    text-transform: uppercase;
    line-height: 1.1;
    white-space: nowrap;
  }
  .holder-title {
    font-weight: 600;
    font-size: 18px;
    margin-bottom: 22px;
  }
  .address {
    font-size: 17px;
    line-height: 1.35;
    margin-bottom: 24px;
    font-style: normal;
  }
  .contact-list { list-style: none; font-size: 17px; line-height: 1.5; }
  .contact-list li { display: flex; align-items: center; gap: 10px; }
  .contact-list svg { width: 14px; height: 14px; flex: none; fill: var(--brand-blue); }
</style>
</head>
<body>
  <section class="card card-back" aria-label="Card back">
    <div class="card-back__pattern" role="img" aria-label="Repeating embossed brand pattern in dark grey"></div>
    <div class="card-back__wordmark">
      <span class="card-back__name">RTAVENOR</span>
      <span class="brand-square"></span>
    </div>
  </section>

  <section class="card card-front" aria-label="Card front">
    <div class="card-front__logo">
      <span class="brand-square"></span>
      <span class="card-front__logo-name">RTavenor</span>
    </div>
    <div class="card-front__details">
      <h1 class="holder-name">Marcus Tavenor</h1>
      <p class="holder-title">Founder/President</p>
      <address class="address">4187 Marlowe Ct. Westbrook,<br>Ohio 27614</address>
      <ul class="contact-list">
        <li><svg viewBox="0 0 16 16"><path d="M3.6 1.5l2.3 2.6-1.3 1.8c.9 1.9 2.4 3.4 4.3 4.3l1.8-1.3 2.6 2.3-1.5 2.3C6.6 13.3 2.7 9.4 1.3 3z"/></svg>(555) 304-0148</li>
        <li><svg viewBox="0 0 16 16"><circle cx="8" cy="8" r="7" fill="none" stroke="#1b78c0" stroke-width="1.6"/><path d="M1 8h14M8 1c-3 3.5-3 10.5 0 14M8 1c3 3.5 3 10.5 0 14" fill="none" stroke="#1b78c0" stroke-width="1.2"/></svg>www.rtavenor.com</li>
        <li><svg viewBox="0 0 16 16"><path d="M1 3h14v10H1z" fill="none" stroke="#1b78c0" stroke-width="1.6"/><path d="M1 3l7 6 7-6" fill="none" stroke="#1b78c0" stroke-width="1.6"/></svg>MRT@RTavenor.com</li>
      </ul>
    </div>
  </section>
</body>
</html>
```